BUSINESS CARD DESIGN

NAME- DALE VORSKIN
PHONE NUMER - 555- 714-9082
EMAIL- OFFICE@TRV-GROUNDMAKRZ.COM
BACK OF CARD- SPEACIALIZES IN LAND CLEARING, FORESTRY MUCLHING AND EXCAVATION

Contact Information for Business Card

NAME- DALE VORSKIN PHONE NUMER - 555- 714-9082 EMAIL- OFFICE@TRV-GROUNDMAKRZ.COM BACK OF CARD- SPEACIALIZES IN LAND CLEARING , MUCLHING AND EXCAVATION

```html
<!DOCTYPE html>
<html lang="en">
<head>
<meta charset="utf-8">
<title>Trevane Groundmakrz LLC — Business Card</title>
<link rel="stylesheet" href="https://fonts.googleapis.com/css2?family=Lato:wght@400;700;900&display=swap">
<style>
  :root {
    --backdrop: #3b3b3d;
    --card-dark: #141416;
    --card-dark-edge: #232326;
    --card-light: #ffffff;
    --ink: #111111;
    --ink-soft: #333333;
    --silver: #e4e4e4;
    --rule-dark: #2a2a3a;
  }
  * { margin: 0; padding: 0; box-sizing: border-box; }
  html, body { width: 1200px; height: 694px; overflow: hidden; }
  body {
    background: var(--backdrop);
    font-family: "Lato", sans-serif;
    position: relative;
  }
  .card {
    position: absolute;
    top: 190px;
    width: 540px;
    height: 314px;
    border-radius: 22px;
    box-shadow: 0 18px 40px rgba(0,0,0,.45);
    overflow: hidden;
  }
  /* Back of card */
  .card-back {
    left: 40px;
    background: linear-gradient(160deg, var(--card-dark-edge), var(--card-dark));
    color: var(--silver);
  }
  .card-back .fold-line {
    position: absolute;
    left: 34px; top: 0; bottom: 0;
    width: 1px;
    background: var(--rule-dark);
  }
  .brand {
    display: flex;
    align-items: center;
    gap: 12px;
    font-weight: 900;
    letter-spacing: .06em;
    text-transform: uppercase;
  }
  .card-back .brand {
    position: absolute;
    top: 86px; left: 0; right: 0;
    justify-content: center;
    font-size: 30px;
    color: var(--silver);
  }
  .brand-dot { width: 26px; height: 26px; border-radius: 50%; background: currentColor; flex: none; }
  .card-back .brand-sub {
    position: absolute;
    top: 138px; left: 0; right: 0;
    text-align: center;
    font-size: 15px;
    font-weight: 700;
    letter-spacing: .5em;
    color: var(--silver);
  }
  .tagline {
    position: absolute;
    bottom: 40px; left: 0; right: 0;
    text-align: center;
    font-size: 17px;
    color: #f2f2f2;
  }
  /* Front of card */
  .card-front {
    left: 620px;
    background: var(--card-light);
    color: var(--ink);
  }
  .card-front .brand {
    position: absolute;
    top: 34px; right: 30px;
    font-size: 20px;
    color: var(--ink);
  }
  .card-front .brand-dot { width: 20px; height: 20px; }
  .card-front .brand-sub {
    position: absolute;
    top: 64px; right: 30px;
    font-size: 11px;
    font-weight: 700;
    letter-spacing: .45em;
  }
  .divider {
    position: absolute;
    height: 1.5px;
    background: var(--ink);
  }
  .divider.top { top: 96px; left: 170px; right: 30px; }
  .address {
    position: absolute;
    top: 110px; right: 30px;
    text-align: right;
    font-size: 15px;
    line-height: 1.35;
    color: var(--ink-soft);
  }
  .person-name {
    position: absolute;
    left: 34px; top: 152px;
    font-size: 22px;
    font-weight: 900;
    letter-spacing: -.01em;
  }
  .person-role {
    position: absolute;
    left: 34px; top: 182px;
    font-size: 15px;
    color: var(--ink-soft);
  }
  .divider.mid { top: 212px; left: 34px; width: 250px; }
  .contact {
    position: absolute;
    left: 34px; top: 224px;
    list-style: none;
    font-size: 15px;
    line-height: 24px;
  }
  .contact li { display: flex; align-items: center; gap: 10px; }
  .contact svg { width: 15px; height: 15px; fill: var(--ink); flex: none; }
</style>
</head>
<body>
  <section class="card card-back" aria-label="Card back">
    <div class="fold-line"></div>
    <div class="brand"><span class="brand-dot"></span>Trevane Groundmakrz</div>
    <div class="brand-sub">LLC · 555-714-9082</div>
    <p class="tagline">Speacializes In Land Clearing , Muclhing And Excavation</p>
  </section>

  <section class="card card-front" aria-label="Card front">
    <div class="brand"><span class="brand-dot"></span>Trevane Groundmakrz</div>
    <div class="brand-sub">LLC · 555-714-9082</div>
    <div class="divider top"></div>
    <p class="address">421, Address line goes here<br>45452, Country name</p>

    <h1 class="person-name">DALE VORSKIN</h1>
    <p class="person-role">Owner</p>
    <div class="divider mid"></div>
    <ul class="contact">
      <li>
        <svg viewBox="0 0 24 24" aria-hidden="true"><path d="M6.6 10.8a15.1 15.1 0 0 0 6.6 6.6l2.2-2.2a1 1 0 0 1 1-.25 11.4 11.4 0 0 0 3.6.57 1 1 0 0 1 1 1V20a1 1 0 0 1-1 1A17 17 0 0 1 3 4a1 1 0 0 1 1-1h3.5a1 1 0 0 1 1 1c0 1.25.2 2.45.57 3.57a1 1 0 0 1-.25 1z"/></svg>
        555- 714-9082
      </li>
      <li>
        <svg viewBox="0 0 24 24" aria-hidden="true"><path d="M2 5h20v14H2z M2 5l10 8 10-8" fill="none" stroke="#111" stroke-width="2.2"/></svg>
        Office@trv-groundmakrz.com
      </li>
      <li>
        <svg viewBox="0 0 24 24" aria-hidden="true"><circle cx="12" cy="12" r="10" fill="none" stroke="#111" stroke-width="2"/><path d="M2 12h20M12 2c3 3 3 17 0 20M12 2c-3 3-3 17 0 20" fill="none" stroke="#111" stroke-width="1.6"/></svg>
        www.websitename.com
      </li>
    </ul>
  </section>
</body>
</html>
```